Psychotherapy, Life Coaching, Writer, Motivational Speaker

I am a psychotherapist, life coach, writer and speaker on health and wellness issues. I am a humanist - who believes that we are born to self-actualize - but life - changes that course. That we develop armor and coping mechanisms that divert our growth. I help people examine their road blocks to happiness. My business is unique in that I do concierge therapy. I work intensively - with multi-day sessions, I work internationally through tele-therapy - and traditionally - in an office space. My work is tailored to your needs.

Target Market(s)

Broad

Industry/Entity Type

Health

Contact Information for Business Card

Listen And Grow
Sam Perriton
248 East 39th Street
New York, NY 10027
(305) 555-0173

Requirements
Must have
• Clean lines... not too busy...
• FB page listing: Listen And Grow
• my Web page: www.listenandgrow-example.com
Nice to have
• I would love to be able to list the services: Psychotherapist, Life Coach, Motivational Speaker and Writer - but also don't want a crazy crowded card. Feel free to use the back for description.
Should not have
• Stay away from corny imagery - lotus flowers, zen, lily pond, clouds.

```html
<!DOCTYPE html>
<html lang="en">
<head>
<meta charset="utf-8">
<title>Listen And Grow – Business Card</title>
<link rel="stylesheet" href="https://fonts.googleapis.com/css2?family=Cinzel:wght@700&family=Lato:wght@400;700&display=swap">
<style>
  :root {
    --page-bg: #e9e9e9;
    --card-bg: #030303;
    --accent-blue: #4d75ab;
    --text-light: #f2f2f2;
    --text-dark: #111111;
    --field-bg: #ffffff;
  }
  * { margin: 0; padding: 0; box-sizing: border-box; }
  html, body {
    width: 1200px; height: 720px; overflow: hidden;
    background: var(--page-bg);
    font-family: "Lato", Arial, sans-serif;
  }
  .canvas { position: relative; width: 1200px; height: 720px; }
  .card {
    position: absolute; top: 241px; width: 419px; height: 239px;
    background: var(--card-bg); border-radius: 14px; color: var(--text-light);
    overflow: hidden;
  }
  .card--front { left: 148px; }
  .card--back { left: 634px; }

  .brand-title {
    position: absolute; top: 58px; left: 0; width: 100%;
    text-align: center; font-family: "Cinzel", Georgia, serif; font-weight: 700;
    font-size: 22px; color: var(--accent-blue); letter-spacing: 0.3px;
  }
  .identity {
    position: absolute; right: 221px; top: 126px; text-align: right;
    font-size: 12px; line-height: 15px; white-space: nowrap;
  }
  .identity__name { font-family: "Cinzel", Georgia, serif; font-weight: 700; font-size: 14px; color: var(--accent-blue); }
  .identity__credentials { font-size: 12px; color: var(--text-light); }
  .identity__line { display: block; }
  .identity__headline { display: block; margin-bottom: 3px; line-height: 18px; }

  .divider {
    position: absolute; left: 207px; top: 123px; width: 2px; height: 70px;
    background: linear-gradient(to bottom, rgba(255,255,255,0), #ffffff 50%, rgba(255,255,255,0));
  }
  .contact-list { position: absolute; left: 214px; top: 128px; list-style: none; }
  .contact-list li { display: flex; align-items: center; height: 16px; font-size: 12px; white-space: nowrap; }
  .contact-list li.contact--large { font-size: 12.5px; }
  .contact-list li.contact--web { font-size: 12px; }
  .contact-list svg { width: 11px; height: 11px; margin-right: 5px; flex: none; }
  .social-square { width: 10px; height: 10px; background: var(--accent-blue); border-radius: 1px; margin-right: 6px; flex: none; }

  .back-title {
    position: absolute; top: 52px; width: 100%; text-align: center;
    font-weight: 700; font-size: 20px; color: var(--accent-blue);
  }
  .appointment-label {
    position: absolute; top: 98px; width: 100%; text-align: center;
    font-weight: 700; font-size: 13px; color: var(--text-light);
  }
  .appointment-field {
    position: absolute; left: 22px; top: 133px; width: 372px; height: 31px;
    background: var(--field-bg); border-radius: 15px; color: var(--text-dark);
    font-size: 13px; display: flex; align-items: center; justify-content: center; white-space: nowrap;
  }
  .appointment-field b { font-weight: 700; }
  .services {
    position: absolute; top: 176px; width: 100%; text-align: center;
    font-size: 13px; color: var(--accent-blue);
  }
</style>
</head>
<body>
<main class="canvas">
  <section class="card card--front" aria-label="Card front">
    <h1 class="brand-title">Listen And Grow</h1>
    <div class="identity">
      <span class="identity__headline"><span class="identity__name">Sam Perriton</span><span class="identity__credentials">, LMHC, NCC</span></span>
      <span class="identity__line">Psychotherapist</span>
      <span class="identity__line">248 East 39th Street</span>
      <span class="identity__line">New York, NY 10027</span>
    </div>
    <div class="divider"></div>
    <ul class="contact-list">
      <li>
        <svg viewBox="0 0 12 12" aria-hidden="true"><path fill="#9aa8bb" d="M1 4c0-2 2-3 5-3s5 1 5 3v1H8V4H4v1H1zM2 6h8l1 5H1z"/></svg>
        (305) 555-0173
      </li>
      <li>
        <svg viewBox="0 0 12 12" aria-hidden="true"><rect x="0.5" y="2" width="11" height="8" fill="#9aa8bb"/><path d="M0.5 2l5.5 4.5L11.5 2" fill="none" stroke="#030303" stroke-width="1"/></svg>
        sperritonglobal@example.com
      </li>
      <li class="contact--web">
        <svg viewBox="0 0 12 12" aria-hidden="true"><g fill="none" stroke="#9aa8bb" stroke-width="1"><circle cx="6" cy="6" r="5"/><ellipse cx="6" cy="6" rx="2.2" ry="5"/><path d="M1 6h10"/></g></svg>
        www.listenandgrow-example.com
      </li>
      <li class="contact--large"><span class="social-square"></span>Listen And Grow</li>
    </ul>
  </section>

  <section class="card card--back" aria-label="Card back">
    <h2 class="back-title">Listen and Grow</h2>
    <p class="appointment-label">Your Next Appoinmet</p>
    <div class="appointment-field">Name..............................<b>Date</b>.......................<b>Time</b>............. am/pm</div>
    <p class="services">Psychotherapy, Coaching, Wellness Media</p>
  </section>
</main>
</body>
</html>
```